Local fast-growing company in the service sector

We are looking for a modern business card design, which should also appear on our letterheads

Target Market(s)

Private and industrial sectors

Contact Information for Business Card

Vorname Name
Kellberger Str. 18
71409 Ostbach
Tel.: 07146-839214-0
Name@agentur-kvtl.de

Colors
9d9d9d
919191
aaaaaa

Requirements
Must have
• The logo (file) in silver

```html
<!DOCTYPE html>
<html lang="de">
<head>
<meta charset="utf-8">
<title>KVTL – Visitenkarte</title>
<link href="https://fonts.googleapis.com/css2?family=Open+Sans:wght@400;700&family=Saira:wght@700&display=swap" rel="stylesheet">
<style>
  :root {
    --backdrop: #d9d9d9;
    --card-dark: #1d1d1f;
    --card-dark-edge: #2a2a2c;
    --card-light: #ffffff;
    --silver: #aaaaaa;
    --silver-mid: #9d9d9d;
    --silver-deep: #919191;
    --text-light: #f4f4f4;
  }
  * { margin: 0; padding: 0; box-sizing: border-box; }
  html, body { width: 1200px; height: 900px; overflow: hidden; }
  body {
    background: var(--backdrop);
    font-family: "Open Sans", Arial, sans-serif;
    display: flex;
    flex-direction: column;
    align-items: center;
    justify-content: center;
    gap: 48px;
  }
  .card {
    width: 640px;
    height: 366px;
    position: relative;
    overflow: hidden;
    box-shadow: 0 10px 30px rgba(0,0,0,0.25);
  }

  /* Front */
  .card-front {
    background: linear-gradient(160deg, var(--card-dark-edge), var(--card-dark));
    display: flex;
    flex-direction: column;
    align-items: center;
    justify-content: center;
  }
  .brand {
    display: flex;
    align-items: center;
    gap: 16px;
  }
  .brand-mark {
    width: 40px;
    height: 40px;
    background: var(--silver);
  }
  .brand-name {
    font-family: "Saira", "Open Sans", sans-serif;
    font-weight: 700;
    font-size: 64px;
    line-height: 1;
    color: var(--silver);
    letter-spacing: 2px;
  }
  .front-web {
    margin-top: 56px;
    color: var(--text-light);
    font-size: 14px;
    letter-spacing: 9px;
  }

  /* Back */
  .card-back { background: var(--card-light); }
  .back-shape { position: absolute; inset: 0; }
  .contact {
    position: absolute;
    left: 36px;
    top: 170px;
    color: var(--text-light);
    font-size: 14px;
    line-height: 1.5;
  }
  .contact-name {
    font-weight: 700;
    font-size: 15px;
    text-transform: uppercase;
    margin-bottom: 2px;
  }
  .contact-line { display: flex; align-items: center; gap: 9px; }
  .contact-line svg { width: 12px; height: 12px; flex: none; }
  .back-brand {
    position: absolute;
    right: 44px;
    top: 172px;
  }
  .back-brand .brand-mark { width: 34px; height: 34px; background: var(--silver-deep); }
  .back-brand .brand-name { font-size: 54px; color: var(--silver-deep); }
</style>
</head>
<body>

  <section class="card card-front" aria-label="Visitenkarte Vorderseite">
    <div class="brand">
      <span class="brand-mark"></span>
      <span class="brand-name">KVTL</span>
    </div>
    <p class="front-web">www.agentur-kvtl.de</p>
  </section>

  <section class="card card-back" aria-label="Visitenkarte Rückseite">
    <svg class="back-shape" viewBox="0 0 640 366" preserveAspectRatio="none" aria-hidden="true">
      <defs>
        <linearGradient id="panel-fill" x1="0" y1="0" x2="1" y2="1">
          <stop offset="0" stop-color="#b4b4b4"/>
          <stop offset="1" stop-color="#9d9d9d"/>
        </linearGradient>
        <linearGradient id="arrow-fill" x1="0" y1="1" x2="1" y2="0">
          <stop offset="0" stop-color="#e6e6e6"/>
          <stop offset="1" stop-color="#bdbdbd"/>
        </linearGradient>
      </defs>
      <path d="M0 0 H355 C340 150 320 280 262 366 H0 Z" fill="url(#panel-fill)"/>
      <path d="M262 366 C320 280 340 150 352 22" fill="none" stroke="url(#arrow-fill)" stroke-width="7"/>
      <polygon points="353,2 368,34 336,30" fill="#cfcfcf"/>
    </svg>

    <div class="contact">
      <p class="contact-name">Lena Hartwig</p>
      <p>Kellberger Str. 18</p>
      <p>71409 Ostbach</p>
      <p class="contact-line">
        <svg viewBox="0 0 16 16" aria-hidden="true"><path fill="#fff" d="M3 1l3 3-2 2c1 2 3 4 5 5l2-2 3 3-2 3C6 14 2 10 1 3z"/></svg>
        07146-839214-0
      </p>
      <p class="contact-line">
        <svg viewBox="0 0 16 16" aria-hidden="true"><rect x="1" y="3" width="14" height="10" fill="#fff"/><path d="M1 3l7 6 7-6" fill="none" stroke="#9d9d9d" stroke-width="1.4"/></svg>
        Name@agentur-kvtl.de
      </p>
      <p class="contact-line">
        <svg viewBox="0 0 16 16" aria-hidden="true"><circle cx="8" cy="8" r="7" fill="#fff"/><path d="M1 8h14M8 1c-3 4-3 10 0 14M8 1c3 4 3 10 0 14" fill="none" stroke="#9d9d9d" stroke-width="1.2"/></svg>
        www.agentur-kvtl.de
      </p>
    </div>

    <div class="brand back-brand">
      <span class="brand-mark"></span>
      <span class="brand-name">KVTL</span>
    </div>
  </section>

</body>
</html>
```